Catalogue Design Project

We need a catalog design for a new private university called Redwell Institute Bayshore (see website www.rwi-bs.org). The catalog should be about 30 pages maximum and will include items such as General Information, Academic schedule, department descriptions, program descriptions, course descriptions, school policies, student services, admissions, San diego Lifestyle, etc.
I will provide the text but I need a professional design with regard to page layouts. I have provided some examples.
Ok, i posted the catalog content, just missing course descriptions.
Target Market(s)
Young Professionals, Foreign Students
Industry/Entity Type
University
Look and feel
Each slider illustrates characteristics of the customer's brand and the style your logo design should communicate.

```html
<!DOCTYPE html>
<html lang="en">
<head>
<meta charset="utf-8">
<title>Academic Programs – Redwell Institute Bayshore</title>
<link rel="stylesheet" href="https://fonts.googleapis.com/css2?family=Carlito:ital,wght@0,400;0,700;1,400;1,700&display=swap">
<style>
  :root {
    --ink: #1c1c1c;
    --navy: #2d5a8c;
    --rule: #8fa4bd;
    --dot-grey: #a9abae;
    --footer-grey: #8a8a8a;
    --paper: #ffffff;
    --parchment-light: #f6f1e6;
    --parchment-mid: #e4dccb;
  }
  html, body {
    margin: 0;
    padding: 0;
    overflow: hidden;
    background: var(--paper);
  }
  .page {
    position: relative;
    width: 927px;
    height: 1200px;
    overflow: hidden;
    background: var(--paper);
    font-family: "Carlito", "Calibri", sans-serif;
    color: var(--ink);
  }
  .header-dots {
    position: absolute;
    left: 58px;
    top: 58px;
  }
  .header-visual {
    position: absolute;
    right: 0;
    top: 0;
    width: 352px;
    height: 146px;
    background: linear-gradient(100deg, rgba(255,255,255,1) 0%, rgba(246,241,230,0.6) 30%, var(--parchment-mid) 70%, var(--parchment-light) 100%);
  }
  .page-title {
    position: absolute;
    left: 306px;
    top: 92px;
    margin: 0;
    font-size: 30px;
    font-weight: 400;
    letter-spacing: 0.5px;
    color: var(--ink);
  }
  .title-bar {
    position: absolute;
    left: 305px;
    top: 133px;
    width: 316px;
    height: 17px;
    background: var(--navy);
  }
  .header-rule {
    position: absolute;
    left: 0;
    top: 150px;
    width: 927px;
    height: 2px;
    background: var(--rule);
  }
  .content {
    position: absolute;
    left: 68px;
    top: 190px;
    width: 791px;
    font-size: 19px;
    line-height: 25.5px;
  }
  .program h2 {
    margin: 0;
    font-size: 22px;
    line-height: 28px;
    font-weight: 700;
  }
  .program h2.sub {
    font-style: italic;
  }
  .program + .program {
    margin-top: 23px;
  }
  .program p {
    margin: 0;
    text-align: justify;
  }
  .audience {
    list-style: none;
    margin: 0;
    padding: 0;
  }
  .audience li {
    position: relative;
    padding-left: 36px;
  }
  .audience li::before {
    content: "•";
    position: absolute;
    left: 0;
  }
  .course-list {
    list-style: none;
    margin: 0;
    padding: 0;
  }
  .footer-rule {
    position: absolute;
    left: 0;
    top: 1155px;
    width: 927px;
    height: 2px;
    background: var(--rule);
  }
  .footer-label {
    position: absolute;
    right: 40px;
    top: 1171px;
    font-size: 13px;
    color: var(--footer-grey);
    letter-spacing: 0.3px;
  }
</style>
</head>
<body>
<div class="page">
  <svg class="header-dots" width="160" height="34" viewBox="0 0 160 34" aria-hidden="true">
    <rect x="0" y="0" width="24" height="12" rx="6" fill="var(--navy)"/>
    <rect x="32" y="0" width="24" height="12" rx="6" fill="var(--dot-grey)"/>
    <rect x="64" y="0" width="24" height="12" rx="6" fill="var(--dot-grey)"/>
    <rect x="96" y="0" width="24" height="12" rx="6" fill="var(--dot-grey)"/>
    <rect x="0" y="20" width="24" height="12" rx="6" fill="var(--dot-grey)"/>
    <rect x="32" y="20" width="24" height="12" rx="6" fill="var(--dot-grey)"/>
    <rect x="64" y="20" width="24" height="12" rx="6" fill="var(--dot-grey)"/>
    <rect x="96" y="20" width="24" height="12" rx="6" fill="var(--dot-grey)"/>
    <rect x="128" y="20" width="24" height="12" rx="6" fill="var(--navy)"/>
  </svg>
  <div class="header-visual" role="img" aria-label="Faded photo of an open book"></div>
  <h1 class="page-title">ACADEMIC PROGRAMS</h1>
  <div class="title-bar"></div>
  <div class="header-rule"></div>

  <main class="content">
    <section class="program">
      <h2>English Language Fluency</h2>
      <p>Redwell Institute Bayshore has on staff well educated and experienced instructors who have lived in other countries and previously spent time learning a foreign language. In addition, our ESL faculty has at least a master's degree in a related field such as Linguistics, English, or TESOL. For these reasons, students at RWIB have the advantage of learning from teachers who are best adapted to getting them to fluency in a short time. Our teachers don't just teach, they do.</p>
      <p>What type of student is appropriate for our fluency program?</p>
      <ul class="audience">
        <li>Visitors who want to complement their travels with study</li>
        <li>Residents who need to improve their language skills for business</li>
        <li>Foreign Students needing to improve test scores for university admission</li>
        <li>Business leaders and executives who interact with English-speaking clients or associates</li>
      </ul>
    </section>

    <section class="program">
      <h2 class="sub">Language Acquisition</h2>
      <p>Coursework focuses on helping students in all areas of communication: reading, writing, listening, and speaking while utilizing American history, culture, and activities for a well-rounded learning experience.</p>
      <p>Hours: 3 hours per week<br>Length: 8 weeks per course<br>Courses:</p>
      <ul class="course-list">
        <li>ENG 100 LEVEL I – FOUNDATIONS</li>
        <li>ENG 200 LEVEL II – GRAMMATICAL CONCEPTS</li>
        <li>ENG 300 LEVEL III – CONVERSATIONAL SKILLS</li>
        <li>ENG 400 LEVEL IV – SENTENCE STRUCTURE</li>
        <li>ENG 500 LEVEL V – ADVANCED FLUENCY</li>
      </ul>
    </section>

    <section class="program">
      <h2 class="sub">ELPE Preparation</h2>
      <p>Coursework for intermediate to advanced levels students wishing to prepare for passing the English-Language-Proficiency Exam college entrance exam. The course focuses on all sections of the actual examination.</p>
      <p>Hours: 3 hours per week<br>Length: 4 weeks per course<br>Courses:</p>
      <ul class="course-list">
        <li>ENG 105 – ELPE: Reading, Structure, and Writing</li>
        <li>ENG 205 – ELPE: Listening and Vocabulary</li>
        <li>ENG 305 – ELPE: Sample Tests</li>
      </ul>
    </section>
  </main>

  <div class="footer-rule"></div>
  <div class="footer-label">6:::&nbsp; REDWELL INSTITUTE</div>
</div>
</body>
</html>
```